copper vale energy ltd commercial solar installs

a bifold A4 brochure , explaining the benefits of solar panel and battery storage on commercial buildings in England

i dont have many images or paragraphs i was hoping that this could be part of your design

```html
<!DOCTYPE html>
<html lang="en">
<head>
<meta charset="utf-8">
<title>Copper Vale Energy – Commercial Solar Brochure</title>
<link href="https://fonts.googleapis.com/css2?family=Montserrat:wght@400;500;600;700;800&display=swap" rel="stylesheet">
<style>
  :root {
    --backdrop: #e3e3e6;
    --paper: #ffffff;
    --ink: #2b2b2b;
    --charcoal: #363636;
    --brand-green: #3db83a;
    --icon-green: #43c23f;
    --light-text: #f2f2f2;
    --photo-dark: #2c3442;
    --photo-mid: #4f5d70;
    --photo-light: #9aa6b3;
  }
  * { margin: 0; padding: 0; box-sizing: border-box; }
  html, body {
    width: 1200px; height: 840px; overflow: hidden;
    background: var(--backdrop);
    font-family: "Montserrat", sans-serif;
    color: var(--ink);
  }
  .spread {
    position: absolute; left: 63px; top: 40px;
    width: 1074px; height: 760px;
    display: flex;
    box-shadow: 0 18px 40px rgba(0,0,0,0.18);
  }
  .page { position: relative; width: 537px; height: 760px; overflow: hidden; }

  /* Left page */
  .page--about { background: var(--paper); }
  .about-text { position: absolute; left: 40px; top: 52px; width: 252px; }
  .section-title {
    color: var(--brand-green); font-weight: 800; font-size: 21px;
    letter-spacing: 0.5px; text-transform: uppercase; margin-bottom: 14px;
  }
  .about-copy { font-size: 11.5px; line-height: 1.6; margin-bottom: 46px; }
  .reasons { list-style: none; }
  .reasons li {
    position: relative; padding-left: 26px;
    font-size: 11.5px; line-height: 1.6; margin-bottom: 12px;
  }
  .reasons svg { position: absolute; left: 0; top: 2px; width: 15px; height: 15px; }
  .about-photo {
    position: absolute; left: 300px; top: 0; width: 237px; height: 642px;
    border-bottom-left-radius: 22px;
    background: linear-gradient(160deg, var(--photo-light) 0%, var(--photo-mid) 35%, var(--photo-dark) 75%, #3b3a2c 100%);
  }
  .green-stripe {
    position: absolute; left: 0; right: 0; height: 12px; background: var(--brand-green);
  }
  .page--about .green-stripe { top: 672px; }

  /* Right page */
  .page--benefits { background: var(--charcoal); }
  .benefits-photo {
    position: absolute; left: 0; top: 0; width: 100%; height: 250px;
    background: linear-gradient(180deg, #5a6470 0%, #7c8790 40%, #8a7d70 75%, #6d6a63 100%);
  }
  .benefits-panel {
    position: absolute; left: 0; top: 190px; width: 100%; height: 570px;
    background: var(--charcoal); border-top-right-radius: 0; border-top-left-radius: 22px;
  }
  .benefits-title {
    position: absolute; left: 40px; top: 218px; width: 420px;
    color: var(--paper); font-weight: 800; font-size: 20px; line-height: 1.25;
    text-transform: uppercase; letter-spacing: 0.4px;
  }
  .benefits { position: absolute; left: 40px; top: 292px; width: 460px; list-style: none; }
  .benefit { display: flex; gap: 14px; margin-bottom: 24px; }
  .benefit-icon {
    flex: none; width: 38px; height: 38px; border-radius: 9px;
    background: var(--icon-green); display: flex; align-items: center; justify-content: center;
  }
  .benefit-icon svg { width: 24px; height: 24px; }
  .benefit-name { color: var(--brand-green); font-weight: 700; font-size: 13px; margin-bottom: 2px; }
  .benefit-copy { color: var(--light-text); font-size: 10.8px; line-height: 1.5; }
  .page--benefits .green-stripe { top: 672px; }
</style>
</head>
<body>
<main class="spread">
  <section class="page page--about">
    <div class="about-text">
      <h2 class="section-title">About Us</h2>
      <p class="about-copy">Copper Vale Energy is a trusted solar installer serving southeast England since 2008. Our qualified experts have over 15 years experience helping homeowners and businesses transition to affordable sustainable solar power.</p>

      <h2 class="section-title">Why Choose Us?</h2>
      <ul class="reasons">
        <li><svg viewBox="0 0 16 16"><rect width="16" height="16" rx="3" fill="#3db83a"/><path d="M4 8.3l2.6 2.6L12 5.4" stroke="#fff" stroke-width="2" fill="none" stroke-linecap="round" stroke-linejoin="round"/></svg>Over 1,000 solar systems installed across residential and commercial properties.</li>
        <li><svg viewBox="0 0 16 16"><rect width="16" height="16" rx="3" fill="#3db83a"/><path d="M4 8.3l2.6 2.6L12 5.4" stroke="#fff" stroke-width="2" fill="none" stroke-linecap="round" stroke-linejoin="round"/></svg>We handle the full process consultations, approval, installations and maintainance.</li>
        <li><svg viewBox="0 0 16 16"><rect width="16" height="16" rx="3" fill="#3db83a"/><path d="M4 8.3l2.6 2.6L12 5.4" stroke="#fff" stroke-width="2" fill="none" stroke-linecap="round" stroke-linejoin="round"/></svg>Approved member of the Solar Installers Guild and Clean Power Installers Network.</li>
        <li><svg viewBox="0 0 16 16"><rect width="16" height="16" rx="3" fill="#3db83a"/><path d="M4 8.3l2.6 2.6L12 5.4" stroke="#fff" stroke-width="2" fill="none" stroke-linecap="round" stroke-linejoin="round"/></svg>Experts stay up-to-date with latest advances in solar technology.</li>
        <li><svg viewBox="0 0 16 16"><rect width="16" height="16" rx="3" fill="#3db83a"/><path d="M4 8.3l2.6 2.6L12 5.4" stroke="#fff" stroke-width="2" fill="none" stroke-linecap="round" stroke-linejoin="round"/></svg>Finance options are available and payback times are greatly reduced.</li>
      </ul>
    </div>
    <div class="about-photo" role="img" aria-label="Installer in hard hat and hi-vis vest carrying a solar panel frame on a rooftop array"></div>
    <div class="green-stripe"></div>
  </section>

  <section class="page page--benefits">
    <div class="benefits-photo" role="img" aria-label="Rows of solar panels on a commercial rooftop beside office buildings"></div>
    <div class="benefits-panel"></div>
    <h2 class="benefits-title">Benefits of solar panels<br>&amp; battery storage</h2>
    <ul class="benefits">
      <li class="benefit">
        <div class="benefit-icon"><svg viewBox="0 0 24 24" fill="none" stroke="#fff" stroke-width="1.6"><circle cx="12" cy="12" r="8"/><path d="M14.5 8.5a2.5 2.5 0 0 0-4.5 1.5v5.5M8.5 12.5h4.5M8.5 15.5h6.5" stroke-linecap="round"/></svg></div>
        <div><h3 class="benefit-name">Financial Savings</h3>
        <p class="benefit-copy">Cut electricity by 50-90% with solar.<br>Earn extra revenue by exporting excess energy to the grid.<br>Use battery storage to utilize energy later instead of sending back to grid.</p></div>
      </li>
      <li class="benefit">
        <div class="benefit-icon"><svg viewBox="0 0 24 24" fill="none" stroke="#fff" stroke-width="1.6" stroke-linecap="round"><path d="M12 4a5.5 5.5 0 0 0-3.2 10v2.5h6.4V14A5.5 5.5 0 0 0 12 4z"/><path d="M9.5 19h5M10.5 21h3"/></svg></div>
        <div><h3 class="benefit-name">Sustainability</h3>
        <p class="benefit-copy">Reduce carbon footprint by using clean renewable solar power.<br>Help address climate change by minimizing fossil fuel use.<br>Enhance corporate social responsibility through renewable energy.</p></div>
      </li>
      <li class="benefit">
        <div class="benefit-icon"><svg viewBox="0 0 24 24" fill="none" stroke="#fff" stroke-width="1.6" stroke-linejoin="round"><path d="M12 3l7 3v5c0 4.5-3 8-7 10-4-2-7-5.5-7-10V6z"/><path d="M8.5 12l2.5 2.5 4.5-5" stroke-linecap="round"/></svg></div>
        <div><h3 class="benefit-name">Resilience</h3>
        <p class="benefit-copy">Add energy security through onsite solar electricity generation.<br>Avoid issues with traditional grid by producing your own power.<br>Battery systems provide backup electricity during outages.</p></div>
      </li>
      <li class="benefit">
        <div class="benefit-icon"><svg viewBox="0 0 24 24" fill="none" stroke="#fff" stroke-width="1.6" stroke-linecap="round"><circle cx="12" cy="10" r="5.5"/><path d="M9 15l-1.5 6 4.5-2 4.5 2L15 15"/></svg></div>
        <div><h3 class="benefit-name">Incentives</h3>
        <p class="benefit-copy">Tax allowance and export guarantee payments incentivize solar investments.<br>Interest free loans and grants improve affordability.<br>Certified professionals ensure quality support.</p></div>
      </li>
    </ul>
    <div class="green-stripe"></div>
  </section>
</main>
</body>
</html>
```